Business Card (double-sided) and Stationary Design for dental office

1) Business Card Design: We need a business card design for a dental specialty office.
Texts should contain:
The name of our office "Brindle Oaks Orthodontics"
Tagline: "Specialist in Orthodontic and Maxillofacial Orthopedics"
Tag line: "Creating "Tolvering" smiles for Children and Adults"
Doctor name: "Doctor Name"
Office Address:
"123 Street Name
City, State Zip code"
Office email address: office@brindleoaksortho.com
Website: www.brindleoaksortho.com

We will provide the full office address once the design is selected
Theme: beach, paradise, coastal, wave
We would like to have some creativity in design. Some acceptable ideas: front page: logo and office name. Back page: more detail information, and map to office in form of an island. Please see sample from our other location, but you DON'T HAVE TO USE OR COPY THE SAME CONCEPT.

IF POSSIBLE, PLEASE SUBMIT AT LEAST TWO CONCEPTS: ONE WITH THE BACK LOOKING SIMILAR TO WHAT IS IN THE SAMPLE, AND ONE DIFFERENT.

Color: designer to choose. We have different shade of blues and sand color in our office. Please see logo.

2) Please also design a matching set of stationary that compliment the business card and our logo.

Target Market(s)

Dental

Contact Information for Business Card

See descriptions

Font styles to use
Other font styles liked:
• Matching texts in logo

Colors
0054AA
0677BA
7BADD7
CADEEF
E8F1F8
0094D4
00A9DD
6FCCEA
C7EBF8
E9F6FB
00AB8E
00BBA5
67D7C9
C6EFE9
E9F9F6

Requirements
Must have
• Double-sided
Nice to have
• Beach coastal theme
Should not have
• Any shape or drawing of of tooth or teeth. We don’t need these. You don't necessarily have to just cut and paste the logo art and text as a whole, you have the liberty to rearrange the text.

```html
<!DOCTYPE html>
<html lang="en">
<head>
<meta charset="utf-8">
<title>Brindle Oaks Orthodontics – Envelope</title>
<link rel="stylesheet" href="https://fonts.googleapis.com/css2?family=Montserrat:wght@700&family=Roboto+Slab:wght@400;700&display=swap">
<style>
  :root {
    --frame-blue: #2856a3;
    --flap-start: #2a5ca8;
    --flap-mid: #2e7fae;
    --flap-end: #44bba9;
    --paper: #ffffff;
    --bubble: #f6f7fb;
    --ink: #0d0d0d;
    --mark-teal: #3f7a8c;
  }
  html, body {
    margin: 0;
    padding: 0;
    width: 1200px;
    height: 825px;
    overflow: hidden;
    background: #ffffff;
  }
  .envelope {
    position: relative;
    width: 1200px;
    height: 825px;
    box-sizing: border-box;
    border: 9px solid var(--frame-blue);
    background: var(--paper);
    overflow: hidden;
  }
  .envelope-art {
    position: absolute;
    left: -9px;
    top: -9px;
    width: 1200px;
    height: 825px;
  }
  .return-address {
    position: absolute;
    left: 239px;
    top: 583px;
    color: var(--ink);
  }
  .office-name {
    margin: 0;
    font-family: "Montserrat", sans-serif;
    font-weight: 700;
    font-size: 21px;
    letter-spacing: 0.4px;
    text-transform: uppercase;
    line-height: 1;
  }
  .doctor-name {
    margin: 17px 0 0;
    font-family: "Roboto Slab", serif;
    font-weight: 700;
    font-size: 19px;
    letter-spacing: 0.5px;
    text-transform: uppercase;
    line-height: 1;
  }
  .address,
  .contact-line {
    margin: 0;
    font-family: "Roboto Slab", serif;
    font-weight: 400;
    letter-spacing: 0.8px;
  }
  .address {
    margin-top: 15px;
    font-size: 19px;
    line-height: 1;
  }
  .contact {
    margin-top: 13px;
    font-size: 18px;
    line-height: 25px;
  }
  .brand-mark {
    position: absolute;
    left: 54px;
    top: 572px;
    width: 154px;
    height: 154px;
    border-radius: 50%;
    background: var(--mark-teal);
  }
</style>
</head>
<body>
  <main class="envelope">
    <svg class="envelope-art" viewBox="0 0 1200 825" aria-hidden="true">
      <defs>
        <linearGradient id="flap-gradient" x1="0" y1="0" x2="1" y2="0">
          <stop offset="0" stop-color="var(--flap-start)"/>
          <stop offset="0.5" stop-color="var(--flap-mid)"/>
          <stop offset="1" stop-color="var(--flap-end)"/>
        </linearGradient>
        <filter id="bubble-shadow" x="-30%" y="-30%" width="160%" height="160%">
          <feDropShadow dx="0" dy="0" stdDeviation="4" flood-color="#c9cddd" flood-opacity="0.35"/>
        </filter>
      </defs>
      <polygon class="flap" points="9,9 1191,9 600,393" fill="url(#flap-gradient)"/>
      <circle cx="485" cy="121" r="50" fill="#ffffff" opacity="0.07"/>
      <g class="bubbles" fill="var(--bubble)" filter="url(#bubble-shadow)">
        <circle cx="178" cy="297" r="50"/>
        <circle cx="651" cy="423" r="50"/>
        <circle cx="1102" cy="377" r="50"/>
        <circle cx="71" cy="538" r="50"/>
        <circle cx="66" cy="850" r="45"/>
        <circle cx="1102" cy="845" r="45"/>
      </g>
    </svg>

    <div class="brand-mark" aria-hidden="true"></div>

    <address class="return-address" style="font-style: normal;">
      <h1 class="office-name">Brindle Oaks Orthodontics</h1>
      <p class="doctor-name">Doctor Name</p>
      <p class="address">123 Street Name City, State Zip code</p>
      <div class="contact">
        <p class="contact-line">office@brindleoaksortho.com</p>
        <p class="contact-line">www.brindleoaksortho.com</p>
      </div>
    </address>
  </main>
</body>
</html>
```